Dynamic Business Card for Sports Supplements Company

Hi! I'm looking for an awesome business card to match my existing sports supplement company. I have uploaded my current company logo and screenshot of the front page of my website.

I would like to have something dynamic and interesting and utilize the colors in the website - the reds and purples

The business card should be double sided and focus on a unique eye-catching design on the back and include all the relevant company info.

Most importantly, it should say somewhere: "Sign up on our website for a coupon code."

Target Market(s)

Mostly for women gym goers but it shouldn't be too feminine. It should be in keeping with the website design. It should flow and clearly be connected to it

Industry/Entity Type

Business

Contact Information for Business Card

Lorraine K. Vestal
CEO
LVestal@Quorvanexco.com
www.quorvanexco.com
555.417.3820
P.O. Box 47315
Halvern, Ohio 00000

Sign up on our website for a coupon code

Font styles to use
Serif
Sans Serif
Other font styles liked:
• Novecento font family and "Quorvanex" is in AR Destine font

Requirements
Must have
• One side should be a bold Quorvanex logo design. Even just the symbol itself may be o.k. (see attached file)

```html
<!DOCTYPE html>
<html lang="en">
<head>
<meta charset="utf-8">
<title>Quorvanex Business Card</title>
<link rel="stylesheet" href="https://fonts.googleapis.com/css2?family=Source+Sans+3:ital,wght@0,400;0,600;0,700;1,400&display=swap">
<style>
  :root {
    --backdrop: #7a5638;
    --card-white: #ffffff;
    --card-black: #0d0d0d;
    --brand-red: #ec1c2b;
    --pattern-red: #e8202e;
    --ink: #1e1e1e;
    --tagline-grey: #8a8a8a;
    --tagline-light: #ffd6d9;
  }
  * { margin: 0; padding: 0; box-sizing: border-box; }
  html, body {
    width: 1200px; height: 987px; overflow: hidden;
    background: var(--backdrop);
    font-family: "Source Sans 3", Arial, sans-serif;
  }
  .canvas { position: relative; width: 1200px; height: 987px; }
  .card {
    position: absolute; left: 293px; width: 615px; height: 350px;
    overflow: hidden; box-shadow: 0 3px 8px rgba(0,0,0,.35);
  }
  .card--front { top: 130px; background: var(--card-white); }
  .card--back { top: 506px; background: var(--brand-red); }

  .front-shapes { position: absolute; inset: 0; }

  .contact { position: absolute; left: 34px; top: 145px; color: var(--ink); }
  .contact__name {
    color: var(--brand-red); font-size: 24px; font-weight: 600;
    letter-spacing: .5px; text-transform: uppercase; line-height: 26px;
  }
  .contact__title { font-size: 18px; line-height: 22px; }
  .contact__address { margin-top: 12px; font-size: 18px; line-height: 21px; }
  .contact__list { list-style: none; margin-top: 6px; font-size: 18px; }
  .contact__item { display: flex; align-items: center; height: 23.5px; }
  .contact__icon { width: 15px; height: 15px; margin-right: 11px; fill: var(--brand-red); }

  .brand-front {
    position: absolute; left: 290px; top: 38px; width: 310px;
    text-align: center; color: var(--card-white);
  }
  .brand-front__mark {
    display: block; width: 66px; height: 66px; margin: 0 auto 25px;
    border-radius: 50%; background: var(--brand-red);
  }
  .brand-front__name {
    font-size: 37px; font-weight: 700; letter-spacing: 1px;
    text-transform: uppercase; line-height: 36px;
  }
  .brand-front__tagline {
    font-size: 11px; letter-spacing: 2.4px; color: var(--tagline-grey);
    text-transform: uppercase; margin-top: 1px;
  }

  .back-pattern { position: absolute; inset: 0; background: var(--pattern-red); }
  .brand-back {
    position: absolute; left: 0; right: 0; top: 136px;
    text-align: center; color: var(--card-white);
  }
  .brand-back__name {
    font-size: 52px; font-weight: 700; letter-spacing: 1.5px;
    text-transform: uppercase; line-height: 50px;
  }
  .brand-back__tagline {
    font-size: 12px; letter-spacing: 3px; color: var(--tagline-light);
    text-transform: uppercase; margin-top: 0;
  }
  .brand-back__offer { font-size: 19px; font-style: italic; margin-top: 0; line-height: 22px; }
</style>
</head>
<body>
<main class="canvas">

  <section class="card card--front" aria-label="Business card front">
    <svg class="front-shapes" width="615" height="350" viewBox="0 0 615 350" aria-hidden="true">
      <polygon points="184,0 615,0 615,350 418,350" fill="var(--card-black)"/>
      <polygon points="170,0 176,0 412,350 406,350" fill="var(--brand-red)"/>
    </svg>

    <div class="contact">
      <h1 class="contact__name">Lorraine K. Vestal</h1>
      <p class="contact__title">CEO</p>
      <p class="contact__address">P.O. Box 47315<br>Halvern, Ohio 00000</p>
      <ul class="contact__list">
        <li class="contact__item">
          <svg class="contact__icon" viewBox="0 0 16 16" aria-hidden="true"><path d="M3.6 1.2l2.3 2.6-1.4 2a9 9 0 0 0 5.7 5.7l2-1.4 2.6 2.3-1.5 2.3C7.4 15 1 8.6 1.3 2.7z"/></svg>
          555.417.3820
        </li>
        <li class="contact__item">
          <svg class="contact__icon" viewBox="0 0 16 16" aria-hidden="true"><path d="M1 3h14v1.4L8 9 1 4.4z M1 6l7 4.6L15 6v7H1z"/></svg>
          LVestal@Quorvanexco.com
        </li>
        <li class="contact__item">
          <svg class="contact__icon" viewBox="0 0 16 16" aria-hidden="true"><circle cx="8" cy="8" r="7"/><path d="M5 4h3l1 2-2 1 1 2 2 1-1 3-2-2-1-2-2-1z M10 3l2 1 1 2-2 0z" fill="#fff"/></svg>
          www.quorvanexco.com
        </li>
      </ul>
    </div>

    <div class="brand-front">
      <span class="brand-front__mark" aria-hidden="true"></span>
      <p class="brand-front__name">Quorvanex</p>
      <p class="brand-front__tagline">Built For Every Workout</p>
    </div>
  </section>

  <section class="card card--back" aria-label="Business card back">
    <div class="back-pattern" role="img" aria-label="Red repeating chevron pattern background"></div>
    <div class="brand-back">
      <p class="brand-back__name">Quorvanex</p>
      <p class="brand-back__tagline">Built For Every Workout</p>
      <p class="brand-back__offer">Sign up on our website for a coupon code</p>
    </div>
  </section>

</main>
</body>
</html>
```